Bright Harbor Counseling Letterhead for hip modern business

I would like some ombre use of the colors in the logo hip letterhead that incorporates logo colors and feel, needs to connect with young professionals and college students. i need to be able to write letters to schools to excuse absences as well. i like color blocks on one side preferably using colors from the attached logo design.

Target Market(s)

high income young people, young adults and college students

Industry/Entity Type

mental health

Font styles to use
Serif
Sans Serif

Colors
0054AA
0677BA
7BADD7
CADEEF
E8F1F8
0094D4
00A9DD
6FCCEA
C7EBF8
E9F6FB
00AB8E
00BBA5
67D7C9
C6EFE9
E9F9F6
59FF00
82FF00
B8FF75
E3FFCB
F4FFEA
A7469A
B969AE
D3A5CF
EDDBEB
F8F0F9
6B429C
8869AF
B7A5CE
E3DAEB
F3F0F8

Requirements
Must have
• a modern hip feel, somewhat color

```html
<!DOCTYPE html>
<html lang="en">
<head>
<meta charset="utf-8">
<title>Bright Harbor Counseling Letterhead</title>
<link rel="stylesheet" href="https://fonts.googleapis.com/css2?family=Open+Sans:wght@300;400;700&display=swap">
<style>
  :root{
    --backdrop:#d9dcdd;
    --paper:#ffffff;
    --plum:#a7469a;
    --violet:#8a3f98;
    --teal:#3fb8c0;
    --ink:#3a3a3a;
    --muted:#6d6d6d;
    --rule:#9a9a9a;
  }
  *{box-sizing:border-box;margin:0;padding:0}
  html,body{width:1200px;height:784px;overflow:hidden}
  body{background:var(--backdrop);font-family:"Open Sans",Arial,sans-serif;display:flex;align-items:center;justify-content:center}
  .letterhead{position:relative;width:560px;height:730px;background:var(--paper);box-shadow:0 2px 10px rgba(0,0,0,.12)}
  .header-stripe{position:absolute;height:9px;background:linear-gradient(var(--violet) 0 62%,var(--teal) 62% 100%)}
  .header-stripe--short{left:0;top:34px;width:48px}
  .header-stripe--long{left:300px;right:0;top:96px}
  .brand{position:absolute;left:60px;top:24px;display:flex;align-items:center;gap:14px}
  .brand-name{font-weight:300;color:var(--ink);line-height:1}
  .brand-name .line1{display:block;font-size:26px}
  .brand-name .line2{display:block;font-size:12px;letter-spacing:3px;margin-top:5px;padding-left:30px;color:var(--muted)}
  .brand-dot{width:30px;height:30px;border-radius:50%;background:var(--plum);margin-top:22px}
  .contact{position:absolute;left:20px;right:20px;top:650px;display:flex;gap:12px;font-size:7.6px;font-weight:700;font-style:normal;color:var(--muted);white-space:nowrap}
  .contact-item{display:flex;align-items:center;gap:3px}
  .contact-item svg{width:9px;height:9px;flex:none}
  .footer-bands{position:absolute;left:0;bottom:0;width:560px;height:66px}
  .web{position:absolute;right:18px;bottom:9px;color:#fff;font-weight:700;font-size:15px;letter-spacing:.2px}
</style>
</head>
<body>
  <main class="letterhead">
    <div class="header-stripe header-stripe--short"></div>
    <div class="brand">
      <h1 class="brand-name"><span class="line1">Bright Harbor</span><span class="line2">Counseling</span></h1>
      <span class="brand-dot"></span>
    </div>
    <div class="header-stripe header-stripe--long"></div>

    <address class="contact">
      <span class="contact-item"><svg viewBox="0 0 10 10"><circle cx="5" cy="5" r="4.6" fill="none" stroke="#a7469a"/><path d="M5 2.3a1.8 1.8 0 0 1 1.8 1.8C6.8 5.4 5 7.7 5 7.7S3.2 5.4 3.2 4.1A1.8 1.8 0 0 1 5 2.3z" fill="#a7469a"/></svg>0000 Example Ave, Ste 210, Oregon, 97201, United States</span>
      <span class="contact-item"><svg viewBox="0 0 10 10"><circle cx="5" cy="5" r="4.6" fill="none" stroke="#a7469a"/><path d="M3.3 2.6l1 .1.4 1.3-.6.5a4 4 0 0 0 1.5 1.5l.5-.6 1.3.4.1 1-.8.6C4.8 7.2 2.8 5.2 2.7 3.4z" fill="#a7469a"/></svg>(000) 000-0000</span>
      <span class="contact-item"><svg viewBox="0 0 10 10"><circle cx="5" cy="5" r="4.6" fill="none" stroke="#a7469a"/><rect x="3" y="3.4" width="4" height="3.4" fill="#a7469a"/></svg>(000) 000-0000</span>
      <span class="contact-item"><svg viewBox="0 0 10 10"><circle cx="5" cy="5" r="4.6" fill="none" stroke="#a7469a"/><rect x="2.8" y="3.4" width="4.4" height="3.2" fill="#a7469a"/><path d="M2.8 3.4L5 5.2l2.2-1.8" fill="none" stroke="#fff" stroke-width=".6"/></svg>info@brightharbor.com</span>
    </address>

    <svg class="footer-bands" viewBox="0 0 560 66" aria-hidden="true">
      <defs>
        <linearGradient id="webFade" x1="0" x2="1" y1="0" y2="0">
          <stop offset="0" stop-color="#a7469a"/>
          <stop offset="1" stop-color="#3fb8c0"/>
        </linearGradient>
      </defs>
      <polyline points="0,10 12,10 18,16 352,16 358,10 560,10" fill="none" stroke="#9a9a9a" stroke-width="2"/>
      <rect x="160" y="20" width="90" height="3" fill="#3fb8c0"/>
      <rect x="0" y="34" width="560" height="32" fill="#8a3f98"/>
      <rect x="0" y="28" width="360" height="4" fill="#a7469a"/>
      <polygon points="368,30 560,30 560,66 352,66" fill="url(#webFade)"/>
    </svg>
    <span class="web">www.brightharbor.com</span>
  </main>
</body>
</html>
```